Coastline Premier Retreats Business Card Design

Design a business card for Coastline Premier Retreats. Look at the website for colors and reference. Card should have logo, name, title, office number, mobile number, email, URL and a tagline like, "Luxury Hotel & Resort Email Marketing" (This might change).

https://www.coastlinepremierretreats.example

The rest I will leave up to your imagination.

Contact Information for Business Card

Logo, name, title, office number, mobile number, email, URL and a tagline like, "Luxury Hotel & Resort Email Marketing" (This might change).

```html
<!DOCTYPE html>
<html lang="en">
<head>
<meta charset="utf-8">
<title>Coastline Premier Retreats – Business Card</title>
<link href="https://fonts.googleapis.com/css2?family=Arimo:wght@400;700&display=swap" rel="stylesheet">
<style>
  :root {
    --orange: #f37423;
    --ink: #1a1a1a;
    --paper: #ffffff;
    --backdrop: #e4e4e4;
  }
  * { box-sizing: border-box; margin: 0; padding: 0; }
  html, body { width: 1200px; height: 856px; overflow: hidden; }
  body {
    background: var(--backdrop);
    font-family: "Arimo", Arial, sans-serif;
    display: flex; align-items: center; justify-content: center; gap: 40px;
  }
  .card {
    position: relative;
    width: 540px; height: 309px;
    box-shadow: 0 10px 28px rgba(0,0,0,.25);
    overflow: hidden;
  }
  .card-front { background: var(--paper); }
  .card-back { background: var(--orange); display: flex; align-items: center; justify-content: center; }

  .front-bands { position: absolute; inset: 0; }

  .brand { position: absolute; left: 28px; top: 98px; display: flex; align-items: center; gap: 8px; white-space: nowrap; }
  .brand-mark { width: 14px; height: 14px; background: var(--orange); flex: none; }
  .brand-name { font-weight: 700; font-size: 17px; color: var(--ink); letter-spacing: .5px; text-transform: uppercase; }

  .person { position: absolute; right: 28px; top: 30px; text-align: right; white-space: nowrap; }
  .person-name { color: var(--orange); font-weight: 700; font-size: 19px; letter-spacing: .5px; }
  .person-title { color: var(--ink); font-size: 13px; margin-top: 2px; }

  .tagline { position: absolute; right: 28px; top: 132px; text-align: right; font-size: 12.5px; color: var(--ink); line-height: 1.3; white-space: nowrap; }

  .contacts { position: absolute; left: 28px; bottom: 66px; list-style: none; }
  .contacts li { display: flex; align-items: center; gap: 8px; font-size: 12.5px; color: var(--ink); line-height: 1.45; white-space: nowrap; }
  .contacts svg { width: 12px; height: 12px; flex: none; }

  .back-brand { display: flex; align-items: center; gap: 14px; white-space: nowrap; }
  .back-brand .brand-mark { width: 22px; height: 22px; background: var(--paper); }
  .back-brand .brand-name { color: var(--paper); font-size: 26px; letter-spacing: 1px; }
</style>
</head>
<body>

<section class="card card-front">
  <svg class="front-bands" viewBox="0 0 540 309" preserveAspectRatio="none" aria-hidden="true">
    <polygon fill="var(--orange)" points="540,186 428,186 414,200 414,252 282,252 282,309 540,309"/>
    <rect x="200" y="250" width="76" height="9" fill="var(--ink)"/>
    <rect x="130" y="252" width="64" height="5" fill="var(--orange)"/>
    <rect x="0" y="290" width="276" height="6" fill="var(--orange)"/>
  </svg>

  <div class="brand">
    <span class="brand-mark"></span>
    <span class="brand-name">Coastline Premier Retreats</span>
  </div>

  <div class="person">
    <p class="person-name">DANIEL MARLOWE</p>
    <p class="person-title">Co-Founder</p>
  </div>

  <p class="tagline">Luxury Hotel &amp; Resort<br>Email Marketing</p>

  <ul class="contacts">
    <li><svg viewBox="0 0 12 12"><path fill="var(--orange)" d="M2.5 1l2 2.3-1 1.2a7 7 0 0 0 4 4l1.2-1 2.3 2-1.3 1.5C5 10.5 1.5 7 .9 2.3z"/></svg>555-014-2718</li>
    <li><svg viewBox="0 0 12 12"><rect x="3" y="0.8" width="6" height="10.4" rx="1.2" fill="none" stroke="var(--orange)" stroke-width="1.3"/><circle cx="6" cy="9.4" r=".7" fill="var(--orange)"/></svg>555-019-3364</li>
    <li><svg viewBox="0 0 12 12"><rect x="0.5" y="2.5" width="11" height="7" fill="var(--orange)"/><path d="M.8 2.8L6 6.8l5.2-4" fill="none" stroke="#fff" stroke-width="1"/></svg>info@coastlinepremierretreats.example</li>
    <li><svg viewBox="0 0 12 12"><circle cx="6" cy="6" r="5.3" fill="none" stroke="var(--orange)" stroke-width="1.2"/><path d="M.8 6h10.4M6 .8c-3 3-3 7.4 0 10.4M6 .8c3 3 3 7.4 0 10.4" fill="none" stroke="var(--orange)" stroke-width=".9"/></svg>www.coastlinepremierretreats.example</li>
  </ul>
</section>

<section class="card card-back">
  <div class="back-brand">
    <span class="brand-mark"></span>
    <span class="brand-name">Coastline Premier Retreats</span>
  </div>
</section>

</body>
</html>
```